Letterhead for a German Distribution/Manufacturing Company

We need a professional Letterhead in a unique Design.
not to playful.
The Letterhead has to show show that we are a international company with headquater in Germany.
all details like adress, Vat Tax Number, Bank Accout, Eori, email, Company number has to be on the Letterhead.
for example use: VAT TAX DE5470318 Bank Account: Kestrel Bank IBAN DE412058731ß204683 Swift: MORV0417352 EORI 3150428697 Company Number: HRB 51806 Adress: VOLMINTA UG Ahornweg 7 Postal Code 06384 City Lindental Country: Germany Email: info@volminta-example.com
the design can be colored but doesnt have to be
Industry/Entity Type
Manufacturing and international distribution
Requirements
Must have
- show that we are a international company with headquater in Germany. our company infos and logo

```html
<!DOCTYPE html>
<html lang="en">
<head>
<meta charset="utf-8">
<title>VOLMINTA Letterhead</title>
<link rel="stylesheet" href="https://fonts.googleapis.com/css2?family=Lato:wght@400;700&family=Dancing+Script:wght@500&display=swap">
<style>
  :root {
    --backdrop: #e6e6e6;
    --paper: #ffffff;
    --ink: #3a3a3a;
    --ink-strong: #222222;
    --rule: #444444;
    --mark: #4a4a4a;
  }
  * { box-sizing: border-box; margin: 0; padding: 0; }
  html, body {
    width: 1200px; height: 874px; overflow: hidden;
    background: var(--backdrop);
  }
  body {
    display: flex; align-items: center; justify-content: center;
    font-family: "Lato", Arial, sans-serif;
    color: var(--ink);
  }
  .letterhead {
    width: 600px; height: 848px;
    background: var(--paper);
    box-shadow: 0 2px 10px rgba(0,0,0,0.12);
    padding: 44px 62px 40px 62px;
    position: relative;
  }
  .brand {
    text-align: center;
  }
  .brand-name {
    display: inline-flex; align-items: center; gap: 10px;
    font-size: 34px; font-weight: 400; letter-spacing: 2px;
    color: var(--mark);
  }
  .brand-dot {
    width: 26px; height: 26px; border-radius: 50%;
    background: var(--mark);
  }
  .company-details {
    margin-top: 6px;
    text-align: center;
    font-size: 8.6px; line-height: 1.45;
    color: var(--ink);
  }
  .header-rule {
    border: 0; border-top: 1.2px solid var(--rule);
    margin: 32px -24px 38px -24px;
  }
  .meta { font-size: 11.5px; line-height: 1.35; }
  .meta p + p { margin-top: 12px; }
  .salutation {
    margin-top: 12px;
    font-size: 13px; font-weight: 700; color: var(--ink-strong);
  }
  .body-copy {
    margin-top: 12px;
    font-size: 11.2px; line-height: 1.38;
  }
  .body-copy p + p { margin-top: 14px; }
  .closing { margin-top: 26px; font-size: 11px; }
  .signature {
    margin-top: 10px;
    font-family: "Dancing Script", cursive;
    font-size: 36px; color: var(--ink-strong);
  }
</style>
</head>
<body>
  <main class="letterhead">
    <header class="brand">
      <div class="brand-name"><span class="brand-dot"></span>VOLMINTA</div>
      <div class="company-details">
        <p>VAT TAX DE5470318</p>
        <p>Bank Account: Kestrel Bank IBAN DE412058731ß204683 Swift: MORV0417352</p>
        <p>EORI 3150428697</p>
        <p>Company Number: HRB 51806</p>
        <p>Adress: VOLMINTA UG Ahornweg 7 Postal Code 06384 City Lindental Country</p>
        <p>Germany Email: info@volminta-example.com</p>
      </div>
    </header>

    <hr class="header-rule">

    <section class="meta">
      <p>January-03-2020</p>
      <p>Mr, Jonas Dreyer<br>President</p>
      <p>Larkfield Corporation<br>123 Street Name, Suite# 10<br>City, State, 120023</p>
    </section>

    <p class="salutation">Dear Mr, Jonas</p>

    <section class="body-copy">
      <p>Lorem ipsum dolor sit amet, consectetur adipisicing elit, sed do eiusmod tempor incididunt ut labore et dolore magna aliqua. Ut enim ad minim veniam, quis nostrud exercitation ullamco laboris nisi ut aliquip ex ea commodo consequat. Duis aute irure dolor in reprehenderit in voluptate velit esse cillum dolore eu fugiat nulla pariatur.</p>
      <p>Lorem ipsum dolor sit amet, consectetur adipisicing elit, sed do eiusmod tempor incididunt ut labore et dolore magna aliqua. Ut enim ad minim veniam, quis nostrud exercitation ullamco laboris nisi ut aliquip ex ea commodo consequat. Duis aute irure dolor in reprehenderit in voluptate velit esse cillum dolore eu fugiat nulla pariatur.</p>
      <p>Lorem ipsum dolor sit amet, consectetur adipisicing elit, sed do eiusmod tempor incididunt ut labore et dolore magna aliqua. Ut enim ad minim veniam, quis nostrud exercitation ullamco laboris nisi ut aliquip ex ea commodo consequat.</p>
      <p>Excepteur sint occaecat cupidatat non proident, sunt in culpa qui officia deserunt mollit anim id est laborum. re et dolore magnam aliquam quaerat voluptatem.</p>
    </section>

    <p class="closing">Regards</p>
    <p class="signature">Henrik Albers</p>
  </main>
</body>
</html>
```